Hollow Thicket, a 3d voxel survival video game needs a card for gaming conventions

I am the lead developer for Hollow Thicket http://www.HollowThicket.example and need a business card to hand out at an indie gaming convention
The card would need to include the game name, website url, my name, position (Lead Developer), e-mail and phone number
The game is a 3d, voxel (with smooth terrain) based survival game with guns and wildlife. The main icon of the game would likely be a grizzly bear but I am willing to accept other designs too.
Attached is a media kit for the game with some images you can use but don't have to its just what little art I can provide. Anything on the website or from the video game can also be used. unrelated art can also be used.
Target Market(s)
Indie Developers/publishers at conferences
Industry/Entity Type
Games
Contact Information for Business Card
Name: Corin Waldrick
Position: Lead Developer
E-mail: Pale_Kettle@mailbox.example
Phone number: 555-372-1186

```html
<!DOCTYPE html>
<html lang="en">
<head>
<meta charset="utf-8">
<title>Hollow Thicket – Business Card</title>
<link rel="stylesheet" href="https://fonts.googleapis.com/css2?family=Source+Sans+3:wght@400;600;700&display=swap">
<style>
  :root {
    --backdrop: #e9e6e2;
    --card-white: #ffffff;
    --card-black: #000000;
    --brand-red: #9b1a12;
    --brand-gold: #a68a4f;
    --ink: #2c2c2c;
    --fur-dark: #4a2e1a;
    --fur-mid: #7a4a2a;
    --fur-light: #a06a40;
  }
  * { box-sizing: border-box; margin: 0; padding: 0; }
  html, body {
    width: 1200px; height: 900px; overflow: hidden;
    background: var(--backdrop);
    font-family: "Source Sans 3", "Myriad Pro", sans-serif;
  }
  .canvas { position: relative; width: 1200px; height: 900px; }

  .card {
    position: absolute;
    overflow: hidden;
    box-shadow: 0 6px 18px rgba(0,0,0,.18);
  }
  .card--front { left: 78px; top: 35px; width: 588px; height: 363px; background: var(--card-white); }
  .card--back  { left: 388px; top: 505px; width: 566px; height: 352px; background: var(--card-black); }

  .bear-art { position: absolute; }
  .card--front .bear-art {
    left: 120px; top: 30px; width: 320px; height: 333px;
    background: radial-gradient(ellipse at 55% 40%, rgba(122,74,42,.22), rgba(122,74,42,.10) 55%, rgba(255,255,255,0) 75%);
  }
  .card--back .bear-art {
    left: 120px; top: 45px; width: 285px; height: 290px;
    background: radial-gradient(ellipse at 55% 45%, var(--fur-light), var(--fur-mid) 40%, var(--fur-dark) 65%, rgba(0,0,0,0) 80%);
  }

  .brand-name {
    position: absolute; left: 0; width: 100%;
    text-align: center;
    font-weight: 700;
    font-size: 46px;
    letter-spacing: 2px;
    text-transform: uppercase;
    color: var(--brand-gold);
  }
  .card--front .brand-name { top: 64px; padding-right: 10px; }
  .card--back .brand-name { top: 142px; font-size: 44px; }

  .contact-block {
    position: absolute; left: 0; top: 186px; width: 100%;
    text-align: center;
    color: var(--ink);
  }
  .person-name { font-size: 20px; font-weight: 600; text-transform: uppercase; letter-spacing: .3px; line-height: 24px; }
  .person-name .first { color: var(--brand-red); }
  .person-name .last { color: var(--brand-gold); }
  .person-role { font-size: 17px; line-height: 22px; }
  .contact-list { list-style: none; margin-top: 26px; font-size: 17px; line-height: 21px; }
  .contact-list li { display: flex; justify-content: center; align-items: center; gap: 4px; }
  .contact-icon { width: 12px; height: 12px; fill: var(--brand-red); }
</style>
</head>
<body>
<main class="canvas">
  <section class="card card--front" aria-label="Business card front">
    <div class="bear-art" role="img" aria-label="Faint photo of a roaring grizzly bear"></div>
    <h1 class="brand-name">Hollow Thicket</h1>
    <div class="contact-block">
      <p class="person-name"><span class="first">Corin</span> <span class="last">Waldrick</span></p>
      <p class="person-role">Lead Developer</p>
      <ul class="contact-list">
        <li>
          <svg class="contact-icon" viewBox="0 0 12 12" aria-hidden="true"><path d="M1 4 Q6 0 11 4 L9 5.5 L8 4.5 Q6 3.8 4 4.5 L3 5.5 Z M2.5 6 H9.5 L10.5 11 H1.5 Z"/></svg>
          555-372-1186
        </li>
        <li>
          <svg class="contact-icon" viewBox="0 0 12 12" aria-hidden="true"><path d="M1 3 H11 V10 H1 Z"/><path d="M1 3 L6 7 L11 3" fill="none" stroke="#fff" stroke-width="1"/></svg>
          Pale_Kettle@mailbox.example
        </li>
        <li>
          <svg class="contact-icon" viewBox="0 0 12 12" aria-hidden="true"><circle cx="6" cy="6" r="5" fill="none" stroke="var(--brand-red)" stroke-width="1.2"/><path d="M1 6 H11 M6 1 Q3 6 6 11 M6 1 Q9 6 6 11" fill="none" stroke="var(--brand-red)" stroke-width="1"/></svg>
          www.HollowThicket.example
        </li>
      </ul>
    </div>
  </section>

  <section class="card card--back" aria-label="Business card back">
    <div class="bear-art" role="img" aria-label="Photo of a roaring grizzly bear on black"></div>
    <p class="brand-name">Hollow Thicket</p>
  </section>
</main>
</body>
</html>
```